Meridale Nutrition needs Stationary and a business card

We would like to use our current logo. The text can be moved around as needed. The stationary needs to be a 'first page' where the logo is more prominent to be impressive on higher quality paper and a second page where the logo is more subtle where there will be much more information on the page. There are 2 clinic locations which will need include name, address, phone number, fax number, web address. The business card should be single sided and contain this information also.
The design must be contemporary and sophisticated as this is a science based diet run out of a medical clinic.

Target Market(s)

People wanting to lose weight, athletes looking to optimise performance, people with arthritis or fighting cancer

Industry/Entity Type

Business

Contact Information for Business Card

must use the logo. I have attached an example card with the practice details on it. there must be space for the doctors name. Also the website www.meridalenutrition.com.au

Requirements
Must have
• the logo, the business adresses and phone numbers, the website, the doctors name and qualifications
Nice to have
• some creativity
Should not have
• Do not simply reproduce the existing card please

```html
<!DOCTYPE html>
<html lang="en">
<head>
<meta charset="utf-8">
<title>Meridale Nutrition – Business Card</title>
<link rel="stylesheet" href="https://fonts.googleapis.com/css2?family=Source+Sans+3:wght@400;600&family=PT+Sans+Narrow&display=swap">
<style>
  :root {
    --backdrop: #3b3b3b;
    --card: #fbfbfb;
    --navy: #2d5a96;
    --sky: #00b4ee;
    --ink: #555555;
    --rule: #8a8a8a;
  }
  * { margin: 0; padding: 0; box-sizing: border-box; }
  html, body {
    width: 1200px; height: 750px; overflow: hidden;
    background: var(--backdrop);
    font-family: "Source Sans 3", sans-serif;
  }
  .canvas { position: relative; width: 1200px; height: 750px; }

  .card {
    position: absolute; left: 250px; top: 176px;
    width: 700px; height: 397px;
    background: var(--card);
    overflow: hidden;
  }

  .locations {
    position: absolute; left: 44px; top: 40px;
    font-size: 15px; line-height: 19px; color: var(--ink);
  }
  .location { margin-bottom: 13px; }
  .location__name, .service__name {
    color: var(--navy); font-weight: 600; font-size: 16px; line-height: 21px;
  }
  .label { color: var(--navy); font-weight: 600; }
  .service { margin-bottom: 4px; }
  .service__link {
    display: inline-block; color: var(--ink);
    border-bottom: 1px solid var(--rule); line-height: 17px;
  }

  .feature-band {
    position: absolute; top: 0; left: 318px;
    width: 78px; height: 397px;
  }

  .brand {
    position: absolute; right: 40px; top: 34px; width: 240px;
    text-align: center;
  }
  .brand__dot {
    display: block; width: 104px; height: 104px; margin: 0 auto 14px;
    border-radius: 50%; background: var(--sky);
    border: 4px solid var(--navy);
  }
  .brand__name {
    color: var(--navy); font-weight: 600; font-size: 22px;
    line-height: 26px; white-space: nowrap;
  }

  .practitioner {
    position: absolute; right: 40px; top: 208px; text-align: right;
  }
  .practitioner__name {
    color: var(--navy); font-weight: 600; font-size: 25px; line-height: 30px;
  }
  .practitioner__credential {
    font-family: "PT Sans Narrow", sans-serif;
    color: var(--sky); font-size: 17px; line-height: 22px;
  }

  .website {
    position: absolute; right: 40px; bottom: 34px;
    color: var(--navy); font-weight: 600; font-size: 16px; line-height: 20px;
  }
</style>
</head>
<body>
<main class="canvas">

  <section class="card">
    <div class="locations">
      <div class="location">
        <div class="location__name">Hollowbay</div>
        <div>52-54 Kestrel Road</div>
        <div>Hollowbay NSW 2190</div>
        <div><span class="label">Tel:</span> 02 9555 0142</div>
        <div><span class="label">Fax:</span> 02 9555 0143</div>
      </div>
      <div class="location">
        <div class="location__name">Linfield Park</div>
        <div>118 Ashgrove Road</div>
        <div>Linfield Park NSW 2044</div>
        <div><span class="label">Tel:</span> 02 9555 0187</div>
        <div><span class="label">Fax:</span> 02 9555 0188</div>
      </div>
      <div class="service">
        <div class="service__name">Shoulder and Elbow</div>
        <span class="service__link">www.elenamarsh.com.au</span>
      </div>
      <div class="service">
        <div class="service__name">Knee surgery</div>
        <span class="service__link">www.kneecareclinic.com.au</span>
      </div>
    </div>

    <svg class="feature-band" viewBox="0 0 78 397" role="img" aria-label="Large brand emblem decoration in blue tones">
      <defs>
        <linearGradient id="bandFill" x1="0" y1="0" x2="1" y2="0">
          <stop offset="0" stop-color="#00b4ee"/>
          <stop offset="1" stop-color="#2d5a96"/>
        </linearGradient>
      </defs>
      <rect width="78" height="397" fill="url(#bandFill)"/>
    </svg>

    <div class="brand">
      <span class="brand__dot"></span>
      <div class="brand__name">Meridale Nutrition</div>
    </div>

    <div class="practitioner">
      <div class="practitioner__name">DR ELENA MARSH</div>
      <div class="practitioner__credential">MBBS (NSW) MBIOMEDE FRACS (ORTHO)</div>
      <div class="practitioner__credential">FAORTHA ORTHOPAEDIC SURGEON</div>
    </div>

    <div class="website">www.meridalenutrition.com.au</div>
  </section>

</main>
</body>
</html>
```